Social Media Graphics - Oakline Push REVISED

Create 6-7 individual social media graphics (square size) to encourage folks to join our online course called:

The Harvest Ledger Circle
How to Launch a Multi-Million Business From Scratch
Sign Up Today!

IMPORTANT: Make the largest and most prominent text on the graphic be: How to Launch a Multi-Million Business From Scratch

For the color scheme of the graphics, let's try a blue color palette; make sure the graphics appeal to both men and women

Make sure each graphic contains 1 of the 3 pics attached (crop pic as needed); and make sure one of the graphics is all TEXT only.

Target Market(s)

men and women looking to start a business

Industry/Entity Type

Entrepreneurship

Colors
0054AA
0677BA
7BADD7
CADEEF
E8F1F8

Requirements
Must have
• All the text and use the 3 pics provided; one graphic can be all text; Simple, modern design that's easy to read

```html
<!DOCTYPE html>
<html lang="en">
<head>
<meta charset="utf-8">
<title>The Harvest Ledger Circle – How to Launch a Multi-Million Business From Scratch</title>
<link rel="stylesheet" href="https://fonts.googleapis.com/css2?family=Anton&family=Oswald:wght@500;600;700&display=swap">
<style>
  :root {
    --sky-top: #0a8fd0;
    --sky-mid: #0068a8;
    --navy-deep: #003a66;
    --panel-fill: #00467a;
    --frame-line: #1e9de8;
    --tab-dark: #1f2b3a;
    --ink-white: #ffffff;
    --accent-blue: #1e9de8;
    --photo-light: #2a8fc9;
    --photo-dark: #1a3a58;
  }
  html, body {
    margin: 0;
    padding: 0;
    width: 1200px;
    height: 1200px;
    overflow: hidden;
    background: var(--navy-deep);
  }
  .promo-canvas {
    display: block;
    width: 1200px;
    height: 1200px;
  }
  .course-tab-label {
    font-family: "Oswald", sans-serif;
    font-weight: 600;
    fill: var(--ink-white);
  }
  .headline-line {
    font-family: "Anton", sans-serif;
    fill: var(--ink-white);
  }
  .cta-text {
    font-family: "Oswald", sans-serif;
    font-weight: 700;
    fill: var(--accent-blue);
  }
</style>
</head>
<body>
<svg class="promo-canvas" viewBox="0 0 1200 1200" xmlns="http://www.w3.org/2000/svg">
  <defs>
    <radialGradient id="bgGlow" cx="600" cy="0" r="1150" gradientUnits="userSpaceOnUse">
      <stop offset="0" stop-color="var(--sky-top)"/>
      <stop offset="0.55" stop-color="var(--sky-mid)"/>
      <stop offset="1" stop-color="var(--navy-deep)"/>
    </radialGradient>
    <linearGradient id="photoTone" x1="0" y1="0" x2="0" y2="1">
      <stop offset="0" stop-color="var(--photo-light)"/>
      <stop offset="1" stop-color="var(--photo-dark)"/>
    </linearGradient>
  </defs>

  <!-- background -->
  <rect class="background" width="1200" height="1200" fill="url(#bgGlow)"/>

  <!-- hosts photo area -->
  <rect class="hosts-photo" x="275" y="90" width="655" height="492" rx="40"
        fill="url(#photoTone)" opacity="0.85"
        role="img" aria-label="Photo of the two course hosts, a man in a black turtleneck with arms crossed and a woman in a denim jacket, both smiling"/>

  <!-- headline panel -->
  <rect class="headline-panel" x="96" y="635" width="1010" height="427" rx="18"
        fill="var(--panel-fill)" fill-opacity="0.55"
        stroke="var(--frame-line)" stroke-width="4"/>

  <!-- course name tab -->
  <rect class="course-tab" x="180" y="581" width="844" height="82" rx="9" fill="var(--tab-dark)"/>
  <text class="course-tab-label" x="602" y="643" font-size="54" text-anchor="middle"
        textLength="770" lengthAdjust="spacingAndGlyphs" letter-spacing="3">THE HARVEST LEDGER CIRCLE</text>

  <!-- headline -->
  <text class="headline-line" x="143" y="798" font-size="128" textLength="907" lengthAdjust="spacingAndGlyphs">HOW TO LAUNCH</text>
  <text class="headline-line" x="143" y="913" font-size="128" textLength="907" lengthAdjust="spacingAndGlyphs">A MULTI-MILLION</text>
  <text class="headline-line" x="143" y="1028" font-size="128" textLength="907" lengthAdjust="spacingAndGlyphs">BUSINESS FROM SCRATCH</text>

  <!-- call to action -->
  <line class="cta-rule" x1="94" y1="1107" x2="428" y2="1107" stroke="var(--accent-blue)" stroke-width="2.5"/>
  <line class="cta-rule" x1="770" y1="1107" x2="1107" y2="1107" stroke="var(--accent-blue)" stroke-width="2.5"/>
  <text class="cta-text" x="600" y="1124" font-size="46" text-anchor="middle"
        textLength="322" lengthAdjust="spacingAndGlyphs">SIGN UP TODAY</text>
</svg>
</body>
</html>
```